Wordpress Design Project

Hi,

I would like a more modern colourful design doing for my website ZAP Lnx (www.za%plnx.com - remove percentage). But I do still want to keep the same sort of colors, just maybe lighter. More interesting.

I want the inside pages to NOT all look the same with just boring text.

I want the site to look more appealing and maybe a new logo.
Updates

I would like to mention I would prefer to keep the same logo after rethinking it (possibly a slight refresh of the logo if you feel its a good idea) and the same color scheme as at present.

Saves us rebranding a lot of our apps, tools online ads etc.

Also I thought it is worth mentioning we have 2 parts to the site. The front end and the logged in area. It would be good if when making the front end you keep in mind the back end at http://p.za%plnx.com (remove percentage). We can only edit this limitedly (can edit the entire footer, the logo and full CSS of it). Would be good if we could make sure the header and footer can be used on the back end as well maybe to make it match.

I also want layouts making not just for the homepage. Obviously every page will basically be the same but I don't want all the other pages to just be 'text' and no real layout.

You can see out main pages on the website at the moment, I want those other pages to be laid out nice and differently as well. For example the testimonials page could be more interesting with speech bubbles and pictures of each person (just use placeholders). The affiliates page could be a description and then a nice fancy list of features why to join etc. 

Nothing overly complicated but I think it makes the whole site seem a lot better.

Target Market(s)

Affiliate Marketing. International.

Requirements
Must have
• Needs to be more room for links across the navigation at the top, also sub menus (at present we have a lot of pages which are hidden deep within other pages).
Nice to have
• Lists of features for advertisers and affiliates on the homepage part.

Menu items and buttons have nice hover over effects.

I want to get across on our pages all the different unique features we have.

Maybe some kind of slider which has past offer logos in, just use example logos.

```html
<!DOCTYPE html>
<html lang="en">
<head>
<meta charset="utf-8">
<title>ZAP Lnx – International Affiliate Network</title>
<link href="https://fonts.googleapis.com/css2?family=Arimo:wght@400;700&display=swap" rel="stylesheet">
<style>
:root{
  --blue-deep:#2a7bb4;
  --blue-mid:#5aa3d3;
  --blue-light:#cfe6f5;
  --heading-blue:#1f6fa5;
  --orange:#f08a12;
  --orange-dark:#e06a05;
  --orange-text:#e5760e;
  --text:#5a5a5a;
  --page:#eeeeee;
  --frame:#d8d8d8;
  --footer:#3c3c3c;
  --footer-text:#e2e2e2;
  --panel:#dcdcdc;
  --white:#ffffff;
}
*{margin:0;padding:0;box-sizing:border-box}
html,body{width:1200px;height:1127px;overflow:hidden}
body{
  position:relative;
  font-family:"Arimo",Arial,sans-serif;
  color:var(--text);
  background:linear-gradient(#ececec 0,#ececec 520px,#f6f6f6 520px);
}
.site{
  position:absolute;left:91px;top:0;width:1018px;height:1127px;
  background:var(--white);
  border-left:1px solid var(--frame);border-right:1px solid var(--frame);
}
.header-band{
  position:absolute;left:95px;top:5px;width:1010px;height:520px;
  background:linear-gradient(180deg,var(--blue-deep) 0,var(--blue-mid) 130px,#9cc9e6 260px,var(--blue-light) 400px,#fff 520px);
}
.header-band::after{
  content:"";position:absolute;left:300px;top:0;width:260px;height:110px;
  background:linear-gradient(100deg,rgba(255,255,255,0) 0,rgba(255,255,255,.18) 50%,rgba(255,255,255,0) 100%);
  transform:skewX(-25deg);
}
.brand{position:absolute;left:112px;top:38px;display:flex;align-items:center;gap:12px}
.brand-mark{width:34px;height:34px;background:var(--orange)}
.brand-name{font-size:34px;font-weight:700;color:var(--white);line-height:40px}
.call{position:absolute;right:109px;top:22px;color:var(--white);font-size:17px;font-weight:700}
.account{position:absolute;left:719px;top:60px;display:flex;gap:5px}
.btn-account{
  height:30px;padding:0 11px;line-height:30px;font-size:14px;color:var(--white);
  background:linear-gradient(#f9a531,var(--orange-dark));border:1px solid #d66a08;border-radius:2px;
}
.search{
  position:absolute;left:872px;top:60px;width:220px;height:30px;background:var(--white);
  border:1px solid #c9d4dc;font-size:11px;color:#777;line-height:28px;padding-left:11px;
}
.search svg{position:absolute;right:8px;top:6px}
.nav{
  position:absolute;left:103px;top:118px;width:994px;height:52px;display:flex;
  background:linear-gradient(#f9a430,var(--orange-dark));border-radius:3px;
  box-shadow:0 2px 3px rgba(0,0,0,.25);
}
.nav a{
  display:block;text-align:center;line-height:52px;color:var(--white);font-size:14.5px;font-weight:700;
  text-decoration:none;border-right:1px solid rgba(255,255,255,.35);
}
.nav a:last-child{border-right:0}
.nav a.current{background:linear-gradient(#f28a1c,#d9600a);border-radius:3px 0 0 3px}
.slider{
  position:absolute;left:103px;top:177px;width:994px;height:340px;background:var(--white);
  border-radius:4px;
}
.slide-title{position:absolute;left:34px;top:49px;font-size:24.5px;font-weight:700;color:var(--heading-blue)}
.slide-text{position:absolute;left:35px;top:90px;width:450px;font-size:13.5px;line-height:23px}
.slide-text p{margin-bottom:13px}
.highlight{color:var(--orange-text)}
.btn-more{
  position:absolute;left:35px;top:234px;width:113px;height:38px;line-height:36px;text-align:center;
  color:var(--white);font-size:15px;font-weight:700;
  background:linear-gradient(#a9a9a9,#7d7d7d);border:1px solid #6f6f6f;border-radius:2px;
}
.dots{position:absolute;left:35px;top:297px;display:flex;gap:7px}
.dots span{width:15px;height:15px;border-radius:50%;background:#3d3d3d}
.dots span.on{background:var(--orange-dark)}
.map{
  position:absolute;left:528px;top:9px;width:459px;height:320px;
  background:radial-gradient(ellipse at 50% 50%,#d9d9d9 0,#ececec 55%,#fff 80%);
}
.about{position:absolute;left:105px;top:555px;width:665px}
.about h2{font-size:18.5px;font-weight:700;color:var(--heading-blue)}
.about h2 span{color:var(--orange-dark)}
.lead{margin-top:15px;color:var(--orange-text);font-size:13.5px}
.about p.body{font-size:13.5px;line-height:23px;margin-top:2px;text-align:justify}
.about-split{position:absolute;left:107px;top:747px;width:434px;font-size:13.5px;line-height:23px;text-align:justify}
.about-photo{
  position:absolute;left:560px;top:749px;width:210px;height:249px;border:3px solid #e6eef4;border-radius:4px;
  background:linear-gradient(160deg,#dceefa 0,#7fb7e0 40%,#3b6f99 75%,#2b3d52 100%);
}
.news{
  position:absolute;left:783px;top:541px;width:313px;height:473px;background:var(--panel);
  border:1px solid #cfcfcf;border-radius:3px;
}
.news-head{position:absolute;left:12px;top:14px;width:290px;height:28px}
.news-head h3{position:absolute;left:38px;top:5px;font-size:18px;font-weight:700;color:var(--heading-blue)}
.news-head .next{position:absolute;right:0;top:7px}
.news-item{
  position:absolute;left:7px;width:297px;height:98px;background:var(--white);border:1px solid #cfcfcf;
  padding:16px 0 0 28px;font-size:13px;line-height:19px;
}
.news-item h4{font-weight:400;color:var(--orange-text);font-size:13.5px;position:relative;margin-bottom:4px}
.news-item h4::before{content:"»";position:absolute;left:-18px;top:-1px;font-size:16px}
.footer{position:absolute;left:95px;top:1031px;width:1010px;height:96px;background:var(--footer);color:var(--footer-text)}
.footer-nav{position:absolute;left:16px;top:22px;font-size:13px}
.footer-nav .sep{margin:0 9px}
.copyright{position:absolute;left:16px;top:60px;font-size:12.5px;word-spacing:2px}
.social{position:absolute;right:15px;top:38px;display:flex;gap:10px}
.social span{width:25px;height:25px;border-radius:3px;background:#4a72b3}
.social span+span{background:#3fb0e0}
</style>
</head>
<body>
<div class="site"></div>
<div class="header-band"></div>

<header>
  <div class="brand">
    <span class="brand-mark"></span>
    <span class="brand-name">ZAP Lnx</span>
  </div>
  <div class="call">Call us : +44 (0)1632 960418</div>
  <div class="account">
    <span class="btn-account">LOG IN</span>
    <span class="btn-account">SIGN UP</span>
  </div>
  <div class="search">Search
    <svg width="16" height="16" viewBox="0 0 16 16"><circle cx="6" cy="6" r="4.5" fill="none" stroke="#222" stroke-width="2"/><line x1="9.5" y1="9.5" x2="14.5" y2="14.5" stroke="#222" stroke-width="3" stroke-linecap="round"/></svg>
  </div>
  <nav class="nav">
    <a class="current" style="width:110px">HOME</a>
    <a style="width:133px">ABOUT US</a>
    <a style="width:133px">OUR BLOG</a>
    <a style="width:163px">TESTIMONIALS</a>
    <a style="width:137px">AFFILIATES</a>
    <a style="width:161px">ADVERTISERS</a>
    <a style="width:157px">CONTACT US</a>
  </nav>
</header>

<section class="slider">
  <h1 class="slide-title">International Affiliate Network</h1>
  <div class="slide-text">
    <p><span class="highlight">Welcome to the ZAP Lnx affiliate network.</span> On time payments, hot &amp; exclusive CPL/CPA offers, fast support and low fees for advertisers, is the making of a leading affiliate network!</p>
    <p>ZAP Lnx offer a wide range of advertisers for your websites. So you can start monetizing your traffic or get an additional revenue stream, today.</p>
  </div>
  <div class="btn-more">View more</div>
  <div class="dots"><span class="on"></span><span></span><span></span><span></span></div>
  <div class="map" role="img" aria-label="Dotted world map with a businessman at the centre and arrows reaching out to orange points on several continents"></div>
</section>

<main>
  <section class="about">
    <h2>About <span>ZAPLNX</span></h2>
    <p class="lead">Suspendisse vitae eros vel mi fermentum pharetra quis non nunc.</p>
    <p class="body">Nulla nec est vitae lorem pharetra facilisis eleifend interdum est. Vivamus ut sapien neque, commodo accumsan magna. Ut commodo sem quis ligula mattis ultricies. Etiam venenatis cursus nulla, nec sagittis nunc aliquet eu. Nulla scelerisque fermentum pulvinar. Aliquam ultricies aliquet elementum. Nam commodo interdum sapien, eget ullamcorper quam vestibulum sed. Vestibulum nunc eros, scelerisque ut ornare ornare, sollicitudin vel tortor. Integer lacinia lorem ut massa porttitor consectetur. Pellentesque sagittis nunc ut elit tempor.</p>
  </section>
  <p class="about-split">Nam commodo interdum sapien, eget ullamcorper quam vestibulum sed. Vestibulum nunc eros, scelerisque ut ornare ornare, sollicitudin vel tortor. Integer lacinia lorem ut massa porttitor consectetur. Pellentesque sagittis nunc ut elit tempor. Pellentesque nisi magna, lobortis in ornare vel, condimentum lobortis nisi. Donec ac eros sit amet diam lobortis mattis hendrerit tempus diam. Nam erat sapien, fermentum nec congue at, porta ut augue. Integer eget sem sem. Proin eros est, ultrices a blandit id, bibendum ut nisl. Fusce at nisi quam. Vestibulum tincidunt metus id tortor cursus pulvinar accumsan quam adipiscing. Phasellus elit est, convallis id pretium eleifend, lacinia viverra ipsum. Nulla pretium dui sit amet dolor vehicula vitae elementum tellus euismod.</p>
  <div class="about-photo" role="img" aria-label="Businessman seen from behind, surrounded by floating blue digital screens"></div>

  <aside class="news">
    <div class="news-head">
      <svg width="28" height="26" viewBox="0 0 28 26"><rect x="2" y="4" width="24" height="20" fill="#eef2f5" stroke="#9aa7b2"/><rect x="5" y="8" width="8" height="6" fill="#7ea6c8"/><line x1="15" y1="9" x2="23" y2="9" stroke="#9aa7b2"/><line x1="15" y1="13" x2="23" y2="13" stroke="#9aa7b2"/><line x1="5" y1="18" x2="23" y2="18" stroke="#9aa7b2"/></svg>
      <h3>Latest News</h3>
      <svg class="next" width="16" height="16" viewBox="0 0 16 16"><circle cx="8" cy="8" r="8" fill="#8a8a8a"/><path d="M6.5 4.5 10 8 6.5 11.5" fill="none" stroke="#fff" stroke-width="2"/></svg>
    </div>
    <article class="news-item" style="top:53px"><h4>Curabitur congue odio vitae</h4>Ligula semper ac auctor justo tincidunt. unc placerat sodales massa non molestie.</article>
    <article class="news-item" style="top:158px"><h4>Curabitur congue odio vitae</h4>Ligula semper ac auctor justo tincidunt. unc placerat sodales massa non molestie.</article>
    <article class="news-item" style="top:263px"><h4>Curabitur congue odio vitae</h4>Ligula semper ac auctor justo tincidunt. unc placerat sodales massa non molestie.</article>
    <article class="news-item" style="top:367px"><h4>Curabitur congue odio vitae</h4>Ligula semper ac auctor justo tincidunt. unc placerat sodales massa non molestie.</article>
  </aside>
</main>

<footer class="footer">
  <div class="footer-nav">Home<span class="sep">|</span>About Us<span class="sep">|</span>Our Blog<span class="sep">|</span>Testimonials<span class="sep">|</span>Affiliates<span class="sep">|</span>Advertisers<span class="sep">|</span>Contact Us</div>
  <div class="copyright">Copyright &copy; 2013 &nbsp; www.zaplnx.com &nbsp; All rights reserved.</div>
  <div class="social"><span></span><span></span></div>
</footer>
</body>
</html>
```